New Alcoholic Spiked Seltzer Line

We need a can design for a line of low calorie alcoholic seltzer. This product is a sparkling water and vodka drink with no sugar added in a slim 12 oz can.

This is a lighter, healthier, alternative to the sugary ready-to-drinks on the market. The product contains only 3 ingredients: Vodka, Water and Natural Flavors. It has only 100 calories but still has 5% alcohol, so you don't need to sacrifice alcohol to cut calories.

This product also does not contain any preservatives.

We want this design to communicate the following objectives to the consumer and in this order:

1. Appetizing product
2.Low calorie
3.Communicate the type of beverage (Spiked Seltzer)

The brand name of the product is VELKA.

The flavor of the product needed to be used for the design is Mango-Orange.

Comparable products are:

www.brindlefizzworks.example/
https://www.quorvabubbles.example
https://pelnavo.example/

The designs should not infringe or copy the creative directions of the products mentionned above. They are only given so that you can better understand the type of product we are developing.

Target Market(s)

Young Professional women between the ages of 25 and 44

Industry/Entity Type

Product

Colors

Designer to choose colors to be used in the design.

Requirements
Must have
• Design extendibility, meaning it can be adapted for other flavors.
• This is a new category in the market we are targeting, so consumers must easily be able to identify what type of product this is.

```html
<!DOCTYPE html>
<html lang="en">
<head>
<meta charset="utf-8">
<title>VELKA Spiked Seltzer – Mango-Orange Can Label</title>
<link rel="stylesheet" href="https://fonts.googleapis.com/css2?family=Carlito:wght@400;700&display=swap">
<style>
  :root {
    --silver-light: #f4f4f4;
    --silver-mid: #d9d9d9;
    --silver-dark: #bdbdbd;
    --wine: #8b1a12;
    --red: #e0202a;
    --dot-orange: #f0a030;
    --band-orange: #e4561f;
    --band-deep: #c84414;
    --band-text: #f9c35a;
    --ink: #2a2a2a;
    --horn-dark: #6e0f0a;
  }
  * { margin: 0; padding: 0; box-sizing: border-box; }
  html, body {
    width: 821px;
    height: 1200px;
    overflow: hidden;
    background: #ffffff;
  }
  .can-label {
    position: relative;
    width: 821px;
    height: 1200px;
    overflow: hidden;
    font-family: "Carlito", "Calibri", sans-serif;
    background: linear-gradient(90deg,
      var(--silver-dark) 0%,
      var(--silver-light) 22%,
      #ffffff 45%,
      var(--silver-light) 70%,
      var(--silver-mid) 100%);
  }
  .halftone-field {
    position: absolute;
    left: 0;
    right: 0;
    top: 0;
    bottom: 120px;
    background: linear-gradient(180deg,
      rgba(240,160,48,0.06) 0%,
      rgba(240,160,48,0.10) 40%,
      rgba(240,160,48,0.35) 70%,
      rgba(232,150,40,0.75) 100%);
  }
  .category {
    position: absolute;
    top: 262px;
    left: 0;
    right: 0;
    text-align: center;
  }
  .category-name {
    color: var(--wine);
    font-size: 66px;
    font-weight: 400;
    line-height: 1;
  }
  .category-tagline {
    color: var(--red);
    font-size: 34px;
    font-weight: 400;
    margin-top: 6px;
  }
  .mascot-art {
    position: absolute;
    top: 400px;
    left: 120px;
    width: 560px;
    height: 300px;
    border-radius: 48% 48% 40% 40%;
    background: radial-gradient(ellipse at 50% 55%,
      #3a3a3a 0%,
      #1c1c1c 30%,
      var(--horn-dark) 62%,
      rgba(139,26,18,0.0) 78%);
  }
  .brand-name {
    position: absolute;
    top: 690px;
    left: 0;
    right: 0;
    text-align: center;
    color: var(--red);
    font-size: 230px;
    font-weight: 700;
    line-height: 1;
    letter-spacing: 4px;
  }
  .flavor {
    position: absolute;
    top: 970px;
    left: 0;
    right: 0;
    text-align: center;
    color: var(--ink);
  }
  .flavor-name {
    font-size: 38px;
    font-weight: 400;
    letter-spacing: 0.5px;
  }
  .flavor-ingredients {
    font-size: 33px;
    font-weight: 400;
    margin-top: 2px;
  }
  .stats-band {
    position: absolute;
    left: 0;
    right: 0;
    bottom: 0;
    height: 120px;
    display: flex;
    align-items: center;
    justify-content: center;
    background: linear-gradient(180deg, var(--band-orange) 0%, var(--band-deep) 100%);
    color: var(--band-text);
    font-size: 36px;
    font-weight: 400;
  }
</style>
</head>
<body>
  <main class="can-label">
    <div class="halftone-field" role="img" aria-label="Orange halftone dot pattern growing denser toward the bottom of the can"></div>

    <header class="category">
      <h1 class="category-name">Spiked Seltzer</h1>
      <p class="category-tagline">low calorie alcoholic seltzer</p>
    </header>

    <div class="mascot-art" role="img" aria-label="Illustration of a ram's head with large curled dark red horns"></div>

    <p class="brand-name">VELKA</p>

    <section class="flavor">
      <h2 class="flavor-name">MANGO-ORANGE</h2>
      <p class="flavor-ingredients">Vodka, Water and Natural Flavors</p>
    </section>

    <footer class="stats-band">5% alcohol - 100 calories</footer>
  </main>
</body>
</html>
```